Support Welcome Packet Redesign

Looking to redesign our current "welcome packet" that we send to our new customers to help them understand our support service. It is currently in Microsoft Word and would like to remain in either word or publisher. Something that we can easily edit, as the content adjusts based on the customer needs. We want this document to be simple and understandable as it should be something our customers can reference at any time during our contract and easy to navigate.

Target Market(s)

Current Customers. Healthcare, Oil & Gas, Transportation, etc.

Industry/Entity Type

It Service

Font styles to use
Sans Serif

Requirements
Must have
• Table of Contents, inVex Logo and current content
Nice to have
• Easy navigation. Redone final page (contact info)

```html
<!DOCTYPE html>
<html lang="en">
<head>
<meta charset="utf-8">
<title>Support Information – inVex</title>
<link href="https://fonts.googleapis.com/css2?family=Carlito:wght@400;700&display=swap" rel="stylesheet">
<style>
  :root{
    --green:#8dc63f;
    --ink:#1a1a1a;
    --grey-text:#4a4a4a;
    --blue:#2e9fd8;
    --footer-ink:#3a3a3a;
  }
  *{margin:0;padding:0;box-sizing:border-box}
  html,body{width:848px;height:1200px;overflow:hidden;background:#fff}
  body{font-family:"Carlito",Calibri,Arial,sans-serif;color:var(--ink)}
  .page{position:relative;width:848px;height:1200px;overflow:hidden;background:#fff}
  .header-art{position:absolute;left:0;top:0;width:848px;height:260px}
  .page-title{position:absolute;left:95px;top:58px;font-size:40px;color:#fff;font-weight:400;letter-spacing:.2px}
  .brand{position:absolute;left:688px;top:104px;width:122px;text-align:center}
  .brand-name{font-size:28px;font-weight:400;color:var(--grey-text);line-height:1}
  .content{position:absolute;left:100px;top:250px;width:648px}
  .section-title{font-size:38px;font-weight:700;color:var(--green);line-height:1.1}
  .section-sub{font-size:17px;font-weight:700;color:var(--ink);margin-top:2px;letter-spacing:.2px}
  .team{margin-top:50px}
  .team + .team{margin-top:27px}
  .team-name{font-size:21px;font-weight:400;line-height:1.1;letter-spacing:.2px}
  .team-name.underlined{text-decoration:underline;text-underline-offset:3px}
  .team-body{font-size:17.2px;line-height:22.8px;letter-spacing:.25px;text-align:justify;margin-top:2px}
  .footer{position:absolute;left:46px;top:1073px;width:756px;height:30px;display:flex;align-items:center;gap:22px;font-size:15px;color:var(--footer-ink)}
  .footer-brand{font-weight:700;font-size:16px;color:var(--footer-ink);margin-right:12px}
  .footer-item{display:flex;align-items:center;gap:6px}
  .footer-item svg{flex:none}
  .footer-rule{position:absolute;left:0;top:1106px;width:848px;height:4px;background:linear-gradient(90deg,var(--blue),var(--green) 30%,#fff 55%,var(--green) 80%,var(--blue))}
  .page-number{position:absolute;left:782px;top:1118px;font-size:16px;font-weight:700}
</style>
</head>
<body>
<div class="page">
  <svg class="header-art" viewBox="0 0 848 260" aria-hidden="true">
    <defs>
      <linearGradient id="headerFade" x1="0" y1="0" x2="0" y2="1">
        <stop offset="0" stop-color="#e9e9e9"/>
        <stop offset="1" stop-color="#ffffff"/>
      </linearGradient>
    </defs>
    <rect width="848" height="260" fill="url(#headerFade)"/>
    <polygon points="0,0 590,0 700,118 0,118" fill="var(--green)"/>
    <rect x="688" y="0" width="122" height="190" fill="#fff"/>
    <polyline points="580,-4 782,236 852,184" fill="none" stroke="var(--green)" stroke-width="9" stroke-linejoin="round"/>
  </svg>

  <h1 class="page-title">Support Information</h1>

  <div class="brand">
    <span class="brand-name">inVex</span>
  </div>

  <main class="content">
    <h2 class="section-title">Support Information</h2>
    <p class="section-sub">inVex Support Teams and Escalation Path</p>

    <section class="team">
      <h3 class="team-name underlined">Technical Support Team</h3>
      <p class="team-body">The technical support team is your first point of contact. The support team will assist with the entry of work tickets for issues and with contacting inVex team members on your escalation path in the case of an urgent issue.</p>
    </section>

    <section class="team">
      <h3 class="team-name">Network Engineering Team</h3>
      <p class="team-body">Our support team includes trained systems and network engineers whose responsibilities include the diagnosis and resolution of complex issues outside of the scope of support provided by the technical support team. The Network Engineering Team is the first point of escalation if the Technical Support Team cannot resolve an issue.</p>
    </section>

    <section class="team">
      <h3 class="team-name">Architecture/Development Team</h3>
      <p class="team-body">The Architecture and Development Team provides advanced support for critical andvhighly complex issues.&nbsp; The Architecture/Development Team acts as the final escalation point for any issues that you may encounter in your environment. This team is also responsible for the design and implementation of new systems required for new work and highly complex issues.</p>
    </section>

    <section class="team">
      <h3 class="team-name underlined">Management Team</h3>
      <p class="team-body">The Management Team serves as the primary point of contact during the implementation or migration phase of a new project, or for any issues that are outside of the scope of the technical support team. However, once the product has moved into your production environment, primary contact should be Technical Support Services for tracking, auditing and response time purposes.</p>
    </section>
  </main>

  <footer class="footer">
    <span class="footer-brand">inVex Technology</span>
    <span class="footer-item">
      <svg width="14" height="18" viewBox="0 0 14 18"><path d="M7 0C3.1 0 0 3.1 0 7c0 5 7 11 7 11s7-6 7-11c0-3.9-3.1-7-7-7z" fill="var(--blue)"/><circle cx="7" cy="7" r="2.6" fill="#fff"/></svg>
      820 W Ridgeway Ave Tempe, AZ 85281
    </span>
    <span class="footer-item">
      <svg width="16" height="16" viewBox="0 0 24 24"><path d="M6.6 10.8a15.1 15.1 0 0 0 6.6 6.6l2.2-2.2c.3-.3.7-.4 1-.2 1.1.4 2.3.6 3.6.6.6 0 1 .4 1 1V20c0 .6-.4 1-1 1A17 17 0 0 1 3 4c0-.6.4-1 1-1h3.5c.6 0 1 .4 1 1 0 1.3.2 2.5.6 3.6.1.3 0 .7-.2 1z" fill="var(--blue)"/></svg>
      480-555-0193
    </span>
    <span class="footer-item">
      <svg width="16" height="16" viewBox="0 0 16 16"><circle cx="8" cy="8" r="7.5" fill="var(--blue)"/><path d="M1 8h14M8 .5c2.2 2 2.2 13 0 15M8 .5c-2.2 2-2.2 13 0 15" stroke="#fff" stroke-width="1" fill="none"/></svg>
      www.invexcorp.example
    </span>
  </footer>
  <div class="footer-rule"></div>
  <div class="page-number">2</div>
</div>
</body>
</html>
```